Creation of a Valterna Flyer design

As part of the cr% 26 # 233; ation of our soci% 26 # 233; t% 26 # 233 ;, we wish to cr% 26 # 233; er a flyer pr% 26 # 233; feeling our diff% 26 # 233; annuities% 26 # 233; s business advisory services% 26 # 233; foreign% 26 # 232; res who wish to develop their activities% 26 # 233; s in Switzerland. We want a double-sided flyer that presents% 26 # 233; society% 26 # 233; t% 26 # 233; d% 26 # 39; a c% 26 # 244; t% 26 # 233; and who presents% 26 # 233; benefits of the other. We have d% 26 # 233; j% 26 # 224; made a very basic provisional flyer to be able to present our activities. We put it to you as an example.

Target Market(s)

European companies% 26 # 233; internal% 26 # 233; res% 26 # 233; es by the market% 26 # 233; Swiss

Industry/Entity Type

Business Consultant

Colors

Designer to choose colors to be used in the design.

Requirements
Must have
• Company name and contact details
A field to detail the services
Nice to have
• Some% 26 # 233; l% 26 # 233; elements that recall Switzerland and some% 26 # 233; l% 26 # 233; elements that recall c% 26 # 244; t% 26 # 233; % 26quot; business% 26quot;

```html
<!DOCTYPE html>
<html lang="en">
<head>
<meta charset="utf-8">
<title>Valterna – Swiss market support</title>
<link rel="stylesheet" href="https://fonts.googleapis.com/css2?family=Inter:ital,wght@0,400;0,600;0,700;1,700&display=swap">
<style>
  :root {
    --navy: #1f3a52;
    --band: #223d51;
    --sky-top: #ffffff;
    --sky-blue: #5f9fe0;
    --sky-soft: #d9e9f7;
    --water: #3f8f9a;
    --white: #ffffff;
    --divider: #7fb3e8;
  }
  * { margin: 0; padding: 0; box-sizing: border-box; }
  html, body { width: 927px; height: 1200px; overflow: hidden; }
  body { font-family: "Inter", Helvetica, Arial, sans-serif; color: var(--navy); }
  .flyer { position: relative; width: 927px; height: 1200px; overflow: hidden; background: var(--sky-top); }
  .scene {
    position: absolute; inset: 0;
    background:
      linear-gradient(180deg, rgba(255,255,255,0) 0%, rgba(255,255,255,0) 66%, #8fb4cf 72%, #c8b9a4 82%, var(--water) 92%),
      linear-gradient(100deg, var(--sky-top) 0%, var(--sky-soft) 40%, #9cc5ee 62%, var(--sky-blue) 100%);
  }
  .headline {
    position: absolute; top: 50px; left: 0; width: 100%;
    text-align: center; font-style: italic; font-weight: 700;
    font-size: 27px; line-height: 34.5px;
  }
  .intro {
    position: absolute; top: 185px; left: 90px; width: 805px;
    font-weight: 700; font-size: 16px; line-height: 22px;
  }
  .services { list-style: none; position: absolute; left: 90px; width: 770px; top: 0; }
  .services li {
    position: absolute; left: 0; width: 770px;
    padding-left: 44px; font-size: 16px; line-height: 22px; text-align: justify;
  }
  .services svg { position: absolute; left: 0; top: 3px; width: 18px; height: 18px; }
  .footer-shape { position: absolute; left: 0; top: 0; width: 927px; height: 1200px; }
  .brand {
    position: absolute; top: 1036px; left: 0; width: 100%;
    display: flex; justify-content: center; align-items: center; gap: 22px;
  }
  .brand-square { width: 39px; height: 39px; border-radius: 7px; background: var(--white); }
  .brand-name { color: var(--white); font-size: 34px; font-weight: 400; letter-spacing: 2px; line-height: 39px; }
  .office {
    position: absolute; top: 1086px; left: 0; width: 100%;
    text-align: center; color: var(--white); font-weight: 600; font-size: 15px; line-height: 20px;
  }
  .contact {
    position: absolute; top: 1140px; left: 0; width: 100%;
    text-align: center; color: var(--white); font-weight: 600; font-size: 17px; letter-spacing: 2px;
  }
  .contact .sep { color: var(--divider); margin: 0 14px; font-weight: 400; }
</style>
</head>
<body>
<main class="flyer">
  <div class="scene" role="img" aria-label="Photo of a sunny blue sky over a Swiss old town riverside with church towers and historic houses"></div>

  <svg class="footer-shape" viewBox="0 0 927 1200" aria-hidden="true">
    <polygon points="0,1132 464,984 927,1128 927,1200 0,1200" fill="var(--band)"/>
    <line x1="0" y1="1133" x2="927" y2="1133" stroke="#3b5870" stroke-width="1"/>
  </svg>

  <h1 class="headline">You are convinced of the potential of your product or<br>service and you wish to focus on the Swiss market,<br>or you want to expand your market share!</h1>

  <p class="intro">Thanks to its personalized approach and tailor-made assistance, Valterna offers you the right support to develop your business activities and answers to all your questions about the swiss market. As a partner we assist you in finding market opportunities:</p>

  <ul class="services">
    <li style="top:275px"><svg viewBox="0 0 18 18"><path d="M3 16 L15 4 M6 3 H15 V12" stroke="var(--navy)" stroke-width="2.4" fill="none"/></svg>By providing commercial contacts that match your target profiles</li>
    <li style="top:321px"><svg viewBox="0 0 18 18"><path d="M3 16 L15 4 M6 3 H15 V12" stroke="var(--navy)" stroke-width="2.4" fill="none"/></svg>By listing the legal and regulatory requirements specific to the Swiss market (Switzerland is not an EU member State);</li>
    <li style="top:388px"><svg viewBox="0 0 18 18"><path d="M3 16 L15 4 M6 3 H15 V12" stroke="var(--navy)" stroke-width="2.4" fill="none"/></svg>By putting you in contact with private or public interlocutors in the context of an individual contact programme;</li>
    <li style="top:455px"><svg viewBox="0 0 18 18"><path d="M3 16 L15 4 M6 3 H15 V12" stroke="var(--navy)" stroke-width="2.4" fill="none"/></svg>By preparing a market study that measures the potential of your product or service;</li>
    <li style="top:501px"><svg viewBox="0 0 18 18"><path d="M3 16 L15 4 M6 3 H15 V12" stroke="var(--navy)" stroke-width="2.4" fill="none"/></svg>By adapting your marketing material (website, brochures, flyers, etc.) to the specific needs of the Swiss market and by translating it into German and/or French;</li>
    <li style="top:567px"><svg viewBox="0 0 18 18"><path d="M3 16 L15 4 M6 3 H15 V12" stroke="var(--navy)" stroke-width="2.4" fill="none"/></svg>By organizing a promotional event that is tailored to your needs;</li>
    <li style="top:614px"><svg viewBox="0 0 18 18"><path d="M3 16 L15 4 M6 3 H15 V12" stroke="var(--navy)" stroke-width="2.4" fill="none"/></svg>By representing you at trade shows or fairs;</li>
    <li style="top:659px"><svg viewBox="0 0 18 18"><path d="M3 16 L15 4 M6 3 H15 V12" stroke="var(--navy)" stroke-width="2.4" fill="none"/></svg>By assuming the fiscal representation of your company</li>
    <li style="top:704px"><svg viewBox="0 0 18 18"><path d="M3 16 L15 4 M6 3 H15 V12" stroke="var(--navy)" stroke-width="2.4" fill="none"/></svg>By offering you logistical and administrative support.</li>
  </ul>

  <div class="brand">
    <span class="brand-square" aria-hidden="true"></span>
    <span class="brand-name">VALTERNA</span>
  </div>

  <address class="office" style="font-style:normal">
    Neuchâtel Office Valterna Sàrl<br>
    Chemin des Saules 14 | 2017 Boudry (Neuchâtel)
  </address>

  <p class="contact">+41 (0)32 000 47 18<span class="sep">|</span>info@valterna.ch<span class="sep">|</span>www.valterna.ch</p>
</main>
</body>
</html>
```